Tellmora Corporate Stationery

Look for design of all new corporate stationery for an existing insurance broking business that is going through a redesign and move from older partners to younger family members. New Logo is attached. Company is Brisbane based.
Colours in the Logo is Hex #43bed8 and website features a lot of hex #17b8d8. Website front page "A plan to protect you" - headline. "Professional and Individual advice to protect your greatest assets" - tagline.

Stationery required: Business Cards, Letter head, Thank-you cards, Birthday cards, Presentation folders, With Compliment slips and a powerpoint template. We also would like to send a card to all customers with the something along of the lines of "something new".

Target Market(s)

Customers of Insurance business looking at superannuation, life and income protection insurance, investment advice and wills

Industry/Entity Type

Insurance Broker

Font styles to use
Other font styles liked:
• same as logo

Requirements
Must have
• The above designs for new stationery for the new business including:
• Business Cards, Letter head, Thank-you cards, Birthday cards, Presentation folders, With Compliment slips and a powerpoint template. We also would like to send a card to all customers with the something along of the lines of "something new".
Nice to have
• It is a new look - long time family business being passed to next generation - big focus on advice for YOU, individual advice etc..

```html
<!DOCTYPE html>
<html lang="en">
<head>
<meta charset="utf-8">
<title>Tellmora Business Card</title>
<link href="https://fonts.googleapis.com/css2?family=Open+Sans:ital,wght@0,400;0,600;1,400&display=swap" rel="stylesheet">
<style>
  :root {
    --backdrop: #262626;
    --card-white: #ffffff;
    --brand-cyan: #43bed8;
    --brand-grey: #838488;
    --text-grey: #6f7073;
    --text-dark: #4a4b4e;
  }
  * { margin: 0; padding: 0; box-sizing: border-box; }
  html, body {
    width: 1200px; height: 987px; overflow: hidden;
    background: var(--backdrop);
    font-family: "Open Sans", Arial, sans-serif;
  }
  .canvas { position: relative; width: 1200px; height: 987px; }

  .card {
    position: absolute; left: 293px; width: 615px; height: 352px;
    overflow: hidden;
  }
  .card-front { top: 130px; background: var(--card-white); }
  .card-back { top: 505px; background: var(--brand-grey); }

  .contact { position: absolute; left: 37px; top: 46px; color: var(--text-dark); }
  .contact-name {
    font-size: 21px; font-weight: 600; color: var(--brand-cyan);
    letter-spacing: 0.3px; line-height: 1.2;
  }
  .contact-title { font-size: 15px; color: var(--text-grey); line-height: 1.4; }
  .contact-email { font-size: 15.5px; line-height: 1.45; }
  .phone-list { list-style: none; margin-top: 14px; }
  .phone-list li {
    display: flex; align-items: center; gap: 8px;
    font-size: 15.5px; line-height: 23px;
  }
  .phone-list svg { width: 15px; height: 15px; fill: var(--brand-cyan); flex: none; }
  .address { margin-top: 16px; font-size: 15.5px; line-height: 22.5px; font-style: normal; }
  .address .web { color: var(--brand-cyan); }

  .brand-front {
    position: absolute; left: 300px; top: 150px; width: 290px;
    display: flex; flex-direction: column; align-items: center; gap: 14px;
  }
  .brand-dot { width: 74px; height: 74px; border-radius: 50%; background: var(--brand-grey); }
  .brand-name {
    font-size: 36px; font-weight: 600; color: var(--brand-cyan);
    letter-spacing: 2px; line-height: 1;
  }

  .front-band { position: absolute; left: 0; bottom: 0; width: 615px; height: 24px; }

  .brand-back {
    position: absolute; right: 36px; top: 200px;
    display: flex; align-items: center; gap: 12px;
  }
  .brand-back .brand-dot { width: 46px; height: 46px; background: var(--card-white); }
  .brand-back .brand-name { color: var(--card-white); font-size: 26px; }
  .back-web {
    position: absolute; right: 30px; top: 308px;
    font-size: 15.5px; font-style: italic; color: var(--card-white);
  }
</style>
</head>
<body>
<div class="canvas">
  <section class="card card-front" aria-label="Business card front">
    <div class="contact">
      <p class="contact-name">DANA WHITLOW</p>
      <p class="contact-title">CEO/FOUNDER</p>
      <p class="contact-email">dana@tellmora.com</p>
      <ul class="phone-list">
        <li>
          <svg viewBox="0 0 16 16" aria-hidden="true"><path d="M3.6 1.2 5.8 3.4c.4.4.4 1 0 1.4L4.7 5.9a9 9 0 0 0 5.4 5.4l1.1-1.1c.4-.4 1-.4 1.4 0l2.2 2.2c.4.4.4 1 0 1.4l-1.2 1.2C11.5 16.1 6.8 13.9 4.4 11.6 2.1 9.2-.1 4.5 1 3.4l1.2-1.2c.4-.4 1-.4 1.4 0z"/></svg>
          <span>555 201 4830</span>
        </li>
        <li>
          <svg viewBox="0 0 16 16" aria-hidden="true"><path d="M4.5 0h7A1.5 1.5 0 0 1 13 1.5v13a1.5 1.5 0 0 1-1.5 1.5h-7A1.5 1.5 0 0 1 3 14.5v-13A1.5 1.5 0 0 1 4.5 0zM5 2v10h6V2zm3 11a.9.9 0 1 0 0 1.8A.9.9 0 0 0 8 13z"/></svg>
          <span>555 372 9146</span>
        </li>
        <li>
          <svg viewBox="0 0 16 16" aria-hidden="true"><path d="M4 1h6l2 2v3H4zM1.5 7h13A1.5 1.5 0 0 1 16 8.5V13h-3v2H3v-2H0V8.5A1.5 1.5 0 0 1 1.5 7zM5 11v3h6v-3z"/></svg>
          <span>555 608 2517</span>
        </li>
      </ul>
      <address class="address">
        214 Wattle Street<br>
        Brisbane, Queensland 4000<br>
        <span class="web">www.tellmora.com</span>
      </address>
    </div>

    <div class="brand-front">
      <span class="brand-dot" aria-hidden="true"></span>
      <span class="brand-name">TELLMORA</span>
    </div>

    <svg class="front-band" viewBox="0 0 615 24" aria-hidden="true">
      <polygon points="0,0 400,0 395,24 0,24" fill="var(--brand-cyan)"/>
      <polygon points="404,0 615,0 615,24 399,24" fill="var(--brand-grey)"/>
    </svg>
  </section>

  <section class="card card-back" aria-label="Business card back">
    <div class="brand-back">
      <span class="brand-dot" aria-hidden="true"></span>
      <span class="brand-name">TELLMORA</span>
    </div>
    <p class="back-web">www.tellmora.com</p>
  </section>
</div>
</body>
</html>
```